Copper Moth Bar & Grill Takeout Menu

Please create a takeout menu using the attached dine-in menu.
Take out menu size: Tri-Fold 11x17

Industry/Entity Type

Bar & Grill (Restaurant)

Colors

Designer to choose colors to be used in the design.

Requirements
Must have
• Phone number and website. "Order Online" "Order for Delivery"
Nice to have
• Area on the back of the menu to feature happy hour specials.

```html
<!DOCTYPE html>
<html lang="en">
<head>
<meta charset="utf-8">
<title>Copper Moth Bar &amp; Grill – Takeout Menu</title>
<link href="https://fonts.googleapis.com/css2?family=Almendra+SC&family=Almendra:wght@400;700&family=Poppins:wght@400;500;600;700&family=Oswald:wght@600&display=swap" rel="stylesheet">
<style>
:root{
  --page:#d9dadb;
  --paper:#eceeed;
  --ink:#1f1f1f;
  --ink-soft:#3a3a3a;
  --panel-dark:#262626;
  --panel-mid:#5e5e5e;
  --frame:#2b2b2b;
  --art:#b9bcbc;
  --art-dark:#8d9091;
  --light:#f3f3f3;
}
*{box-sizing:border-box;margin:0;padding:0}
html,body{width:1200px;height:2250px;overflow:hidden;background:var(--page)}
body{font-family:"Poppins",sans-serif;color:var(--ink);position:relative}
.spread{position:absolute;left:50px;width:1100px;height:708px;background:var(--paper);box-shadow:0 2px 8px rgba(0,0,0,.18)}
.spread--outside{top:278px}
.spread--inside{top:1264px}
.frame{position:absolute;inset:22px;border:2px solid var(--frame);}
.frame::before{content:"";position:absolute;inset:3px;border:7px solid #6f7272}
.frame::after{content:"";position:absolute;inset:12px;border:1.5px solid var(--frame)}
.abs{position:absolute}
.banner{position:absolute;height:25px;background:var(--panel-dark);color:var(--light);font-family:"Almendra SC",serif;font-size:17px;letter-spacing:.5px;display:flex;align-items:center;justify-content:center;outline:1.5px solid var(--panel-dark);outline-offset:2px}
.banner::after{content:"";position:absolute;inset:2px;border:1px solid #cfcfcf}
.note{font-size:9.5px;text-align:center;line-height:1.2;color:var(--ink-soft)}
.item{font-size:8.6px;line-height:1.17;margin-bottom:5px;color:var(--ink-soft)}
.item__head{display:flex;justify-content:space-between;font-weight:700;color:var(--ink);font-size:8.6px}
.item__head span:last-child{font-weight:600}
.opt{display:flex;justify-content:space-between}
.leader{display:flex;align-items:baseline;font-size:10.5px;line-height:1.18}
.leader span:nth-child(2){flex:1;border-bottom:1px dotted var(--ink);margin:0 2px;transform:translateY(-3px)}
.leader span:last-child{font-weight:700}
.optbox{position:absolute;top:307px;width:87px;height:126px;background:var(--panel-mid);color:var(--light);border:1px solid #888;outline:1px solid var(--panel-mid);outline-offset:2px;text-align:center;padding:10px 4px}
.optbox h3{font-family:"Almendra SC",serif;font-weight:400;font-size:10.5px;margin-bottom:8px;border-bottom:1px solid #aaa;padding-bottom:3px}
.optbox p{font-size:7px;line-height:1.3}
.art{position:absolute;background:linear-gradient(160deg,var(--art),var(--art-dark));border-radius:6px;opacity:.85}
.wordmark{position:absolute;font-family:"Almendra",serif;font-weight:700;color:var(--ink);text-align:center;line-height:1}
.site{position:absolute;font-size:13px;letter-spacing:1px;text-align:center;font-weight:500}
.contact{position:absolute;left:413px;top:180px;width:270px;height:253px;background:var(--panel-dark);color:var(--light);border-radius:4px;outline:1.5px solid var(--panel-dark);outline-offset:3px;text-align:center}
.contact__icon{width:24px;height:24px;margin:0 auto}
.contact__phone{font-weight:700;font-size:11.5px;letter-spacing:1px;margin:4px 0 12px}
.contact__addr{font-weight:700;font-size:11.5px;letter-spacing:1px;line-height:1.35;margin-top:4px}
.happy{position:absolute;left:0;right:0;top:160px;display:flex;justify-content:center;align-items:flex-end;gap:4px}
.happy__small{font-family:"Oswald",sans-serif;font-size:13px;writing-mode:vertical-rl;transform:rotate(180deg);letter-spacing:1px;color:#cfcfcf}
.happy__big{font-family:"Oswald",sans-serif;font-size:56px;line-height:.95;letter-spacing:-1px}
.happy__when{position:absolute;left:0;right:0;top:226px;font-size:8px;font-weight:700}
.notice{position:absolute;left:434px;top:455px;width:229px;height:65px;border:1.5px solid var(--ink);border-radius:7px;font-size:8.4px;font-weight:700;text-align:center;line-height:1.22;padding:11px 10px 0}
.cta{position:absolute;left:785px;top:590px;width:260px;height:33px;background:var(--panel-dark);color:var(--light);font-family:"Almendra SC",serif;font-size:21px;letter-spacing:1.5px;display:flex;align-items:center;justify-content:center;outline:1.5px solid var(--panel-dark);outline-offset:2px}
.cta::after{content:"";position:absolute;inset:2px;border:1px solid #cfcfcf}
.addbox{position:absolute;left:54px;top:415px;width:258px;height:49px;background:var(--panel-dark);color:var(--light);padding:6px 12px;font-size:9.5px;line-height:1.2;outline:1px solid var(--panel-dark);outline-offset:2px}
.addbox .opt span:first-child{flex:1;border-bottom:1px dotted #ccc;margin-right:6px}
.dress{position:absolute;left:54px;top:490px;width:258px;height:88px;border:1.5px solid var(--ink);border-radius:8px;text-align:center;font-size:9px;line-height:1.2;padding:13px 8px 0}
.dress__title{position:absolute;top:-12px;left:50%;transform:translateX(-50%);background:var(--paper);padding:0 8px;font-family:"Almendra",serif;font-weight:700;font-size:17px;font-style:normal}
.burgerhead{position:absolute;left:790px;top:45px;width:246px;height:63px;background:var(--panel-dark);color:var(--light);font-family:"Almendra SC",serif;font-size:18px;line-height:1.1;text-align:center;display:flex;align-items:center;justify-content:center;outline:1.5px solid var(--panel-dark);outline-offset:2px}
.burgerhead::after{content:"";position:absolute;inset:3px;border:1px solid #cfcfcf}
.col{position:absolute}
</style>
</head>
<body>

<!-- Outside spread -->
<section class="spread spread--outside" aria-label="Outside panels">
  <div class="frame"></div>

  <!-- Handhelds panel -->
  <div class="banner" style="left:73px;top:61px;width:235px">OTHER HANDHELDS</div>
  <p class="note abs" style="left:58px;top:96px;width:265px">All served with Hand Cut Fries or Sweet Potato Fries.<br>Premium sides available for an up charge +2</p>
  <div class="col" style="left:50px;top:128px;width:258px">
    <div class="item"><div class="item__head"><span>CAT CLUB</span><span>12</span></div>Sliced whole wheat bread with roasted garlic aioli, grilled marinated chicken breast, provolone cheese bacon, lettuce and tomato.</div>
    <div class="item"><div class="item__head"><span>SOUTHWEST MELT</span><span>12</span></div>Sliced whole wheat bread with roasted garlic aioli,3 pepper colby jack, roasted red peppers and corn.</div>
    <div class="item"><div class="item__head"><span>WHAT'S GOUDA?</span><span>12</span></div>Sliced whole wheat bread with roasted garlic aioli smoked gouda and provolone cheeses, roasted red peppers and portobello mushrooms.</div>
    <div class="item"><div class="item__head"><span>WESTOVER MELT</span><span>12</span></div>Sliced whole wheat bread with roasted garlic aioli, zucchini, portobello mushrooms, red peppers, with melted brie and provolone cheeses.</div>
  </div>
  <div class="optbox" style="left:51px"><h3>CHEESES</h3><p>Vermont Cheddar | Smoked Gouda 3-Pepper Colby Jack Monterey Jack | Swiss | Brie Provolone | American</p></div>
  <div class="optbox" style="left:142px"><h3>CONDIMENTS</h3><p>Horseradish Aioli | Chipotle Crema | Roasted Garlic Aioli | Citrus Aioli Spicy Ketchup | Dijon Mustard | Yellow Mustard | Mayo | Ketchup</p></div>
  <div class="optbox" style="left:233px"><h3>TOPPINGS</h3><p>Bacon | Shrimp | Egg | Red Onion | White Onion | Portobello Mushrooms | Roasted Corn | Roasted Red Peppers Guacamole | Pico De Gallo | Fresh or Pickled Jalapenos</p></div>

  <div class="banner" style="left:93px;top:451px;width:195px">SIDES</div>
  <div class="col" style="left:55px;top:490px;width:252px">
    <div class="leader"><span>Potato Salad</span><span></span><span>$4</span></div>
    <div class="leader"><span>Fire Roasted Veggies</span><span></span><span>$6</span></div>
    <div class="leader"><span>Brown Rice, Quinoa, &amp; Kale Medley</span><span></span><span>$5</span></div>
  </div>
  <div class="banner" style="left:93px;top:548px;width:195px">KIDS MENU</div>
  <p class="note abs" style="left:55px;top:582px;width:252px">All served with French Fries</p>
  <div class="col" style="left:55px;top:598px;width:252px">
    <div class="leader"><span>Grilled Cheese</span><span></span><span>14</span></div>
    <div class="leader"><span>Cheese Quesadilla</span><span></span><span>16</span></div>
    <div class="leader"><span>Mac &amp; Cheese</span><span></span><span>16</span></div>
    <div class="leader"><span>Chicken Tenders</span><span></span><span>14</span></div>
  </div>

  <!-- Contact panel -->
  <div class="art" role="img" aria-label="Illustration of two cartoon characters toasting with drinks" style="left:475px;top:42px;width:150px;height:140px"></div>
  <div class="contact">
    <div style="padding-top:28px">
      <svg class="contact__icon" viewBox="0 0 24 24" aria-hidden="true"><circle cx="12" cy="12" r="12" fill="#f3f3f3"/><path d="M8.2 6.5l2 .2.9 2.4-1.2 1a7 7 0 003 3l1-1.2 2.4.9.2 2c-.6.9-1.6 1.2-2.6 1A9 9 0 017.2 9c-.2-1 .1-2 1-2.5z" fill="#262626"/></svg>
      <div class="contact__phone">555-014-2290</div>
      <svg class="contact__icon" viewBox="0 0 24 24" aria-hidden="true"><circle cx="12" cy="12" r="12" fill="#f3f3f3"/><path d="M12 5a4.5 4.5 0 00-4.5 4.5c0 3.3 4.5 8.5 4.5 8.5s4.5-5.2 4.5-8.5A4.5 4.5 0 0012 5zm0 6.3a1.8 1.8 0 110-3.6 1.8 1.8 0 010 3.6z" fill="#262626"/></svg>
      <div class="contact__addr">1420 Linden Row,<br>Fairview, VA 22000</div>
    </div>
    <div class="art" role="img" aria-label="Sketch of a hand holding a wine glass" style="left:8px;top:170px;width:62px;height:40px;opacity:.45"></div>
    <div class="art" role="img" aria-label="Sketch of a hand holding a glass" style="left:206px;top:170px;width:54px;height:40px;opacity:.45"></div>
    <div class="happy"><span class="happy__small">HAPPY</span><span class="happy__big">HOUR</span></div>
    <div class="happy__when">EVERY FRIDAY FROM 4PM TO 8PM</div>
  </div>
  <div class="art" role="img" aria-label="Small chili pepper icon" style="left:535px;top:443px;width:28px;height:10px;border-radius:6px"></div>
  <div class="notice">*The consumption of raw or undercooked eggs, meat, poultry, seafood or shellfish may contribute to food borne illness, especially if you have a medical condition. - Vegetarian - Spicy</div>
  <div class="wordmark" style="left:448px;top:545px;width:200px;font-size:21px;line-height:1.05">Copper Moth<br>Bar &amp; Grill</div>
  <div class="site" style="left:413px;top:641px;width:270px">www.coppermothgrill.com</div>

  <!-- Cover panel -->
  <div class="wordmark" style="left:790px;top:68px;width:250px;font-size:30px;line-height:1.05">Copper Moth<br>Bar &amp; Grill</div>
  <div class="art" role="img" aria-label="Illustration of two cartoon characters drinking beside a sandwich, burger and cocktail" style="left:760px;top:206px;width:312px;height:242px"></div>
  <div class="wordmark" style="left:770px;top:462px;width:290px;font-size:44px;line-height:1.05">Copper Moth<br>Bar &amp; Grill</div>
  <div class="abs" style="left:880px;top:566px;width:70px;height:5px;border-radius:3px;background:var(--ink)"></div>
  <div class="abs" style="left:780px;top:568px;width:270px;height:1px;background:#777"></div>
  <div class="cta">ORDER DELIVERY</div>
  <div class="site" style="left:785px;top:641px;width:260px">www.coppermothgrill.com</div>
</section>

<!-- Inside spread -->
<section class="spread spread--inside" aria-label="Inside panels">
  <div class="frame"></div>

  <div class="banner" style="left:93px;top:45px;width:196px">SALADS</div>
  <div class="col" style="left:54px;top:84px;width:258px">
    <div class="item"><div class="item__head"><span>COMBO CAT</span><span>16</span></div>Enjoy a side House and a cup of any soup.</div>
    <div class="item"><div class="item__head"><span>CAT HOUSE SALAD</span><span>16</span></div>Spring lettuce mix, fresh red peppers, onion, cherry tomatoes, cucumber, and croutons. Served with Red Wine Vinaigrette.</div>
    <div class="item"><div class="item__head"><span>GRILLED CHICKEN SALAD</span><span>16</span></div>Spring lettuce mix, grilled chicken breast, bacon, fresh red peppers, onions, tomatoes, cucumber and feta cheese. Served with Red Wine Vinaigrette.</div>
    <div class="item"><div class="item__head"><span>GRILLED SHRIMP SALAD*</span><span>16</span></div>Spring lettuce mix, garlic Roasted Shrimp, roasted corn, pico de gallo fresh avocado, Served with Lemon Champagne Vinaigrette.</div>
    <div class="item"><div class="item__head"><span>GOAT CHEESE SALAD</span><span>16</span></div>Spring lettuce mix, fried goat cheese, fresh red peppers, cranberries, white onions, and cherry tomatoes.</div>
    <div class="item"><div class="item__head"><span>THE SKINNY CAT</span><span>16</span></div>Spring lettuce mix, sliced apple, sun dried cranberries, roasted corn, cherry tomatoes, and feta cheese.</div>
    <div class="item"><div class="item__head"><span>SMALL HOUSE SALAD</span><span>16</span></div>Spring lettuce mix, sliced apple, sun dried cranberries, roasted corn, cherry tomatoes, and feta cheese.</div>
  </div>
  <div class="addbox">
    <div class="opt"><span><b>Add:</b> Grilled Chicken</span><span>5</span></div>
    <div class="opt"><span>Garlic Roasted Shrimp</span><span>5</span></div>
    <div class="opt"><span>Fried Goat Cheese</span><span>4</span></div>
  </div>
  <div class="dress"><span class="dress__title">Dressings</span>Balsamic Vinaigrette | Caesar<br>Red Wine Vinaigrette | Honey-Mustard | Lemon Champagne Vinaigrette | Ranch | Blue Cheese<br>Served with Balsamic Vinaigrette.<br>Served with Lemon Champagne Vinaigrette</div>
  <div class="art" role="img" aria-label="Sketch of a bottle, sandwich and burger on a plate" style="left:107px;top:584px;width:182px;height:100px"></div>

  <div class="banner" style="left:452px;top:45px;width:196px">STARTERS</div>
  <div class="col" style="left:410px;top:77px;width:280px">
    <div class="item"><div class="item__head"><span>TORTILLA CHIPS</span><span></span></div>
      <div class="opt"><span>with House-made Salsa Verde</span><span>7</span></div>
      <div class="opt"><span>with House-made Fire Roasted Salsa</span><span>7</span></div>
      <div class="opt"><span>with Guacamole &amp; Pico De Gallo</span><span>8</span></div>
      <div class="opt"><span>with Queso</span><span>8</span></div>
      <div class="opt"><span>with Chili con Queso</span><span>9</span></div></div>
    <div class="item"><div class="item__head"><span>WINGS</span><span></span></div>
      <div class="opt"><span>8 pieces</span><span>7</span></div>Flash-fried to a crispy golden brown and tossed in your choice of sauce. Choose from our Signature Hot, or Mild Sauce, or BBQ. Your choice of ranch or blue cheese.</div>
    <div class="item"><div class="item__head"><span>QUESADILLAS</span><span></span></div>
      <div class="opt"><span>Cheddar and Monterey Jack Cheese</span><span>12</span></div>
      <div class="opt"><span>Pulled Marinated Chicken &amp; Cheese</span><span>16</span></div>
      <div class="opt"><span>Fire Roasted Vegetables &amp; Cheese</span><span>14</span></div>
      <div class="opt"><span>Garlic Roasted Shrimp &amp; Cheese</span><span>16</span></div>
      All quesadillas are stuffed with roasted red peppers, black beans and your choice below. Served with guacamole, pico de gallo, and chipotle crema on the side.</div>
    <div class="item"><div class="item__head"><span>CLAW-FULL NACHOS</span><span></span></div>
      Tortilla chips, melted white queso, Cheddar and Monterey Jack cheeses, pico de gallo, guacamole, chipotle sour cream, jalapenos, black beans, &amp; green onions
      <div class="opt"><span>Copper Moth Chili Nachos</span><span>14</span></div>
      <div class="opt"><span>Pulled Chicken Nachos</span><span>16</span></div>
      <div class="opt"><span>Garlic Roasted Shrimp</span><span>16</span></div>
      <div class="opt"><span>Fire Roasted Vegetables Nachos</span><span>14</span></div></div>
    <div class="item"><div class="item__head"><span>FRENCH FRIES</span><span></span></div>
      Served with our house made Garlic Aioli and Spicy Ketchup.
      <div class="opt"><span>Fries Only</span><span>7</span></div>
      <div class="opt"><span>Sweet Potato Fries</span><span>7</span></div>
      <div class="opt"><span>Cheddar-Jack Cheese Fries</span><span>8</span></div>
      <div class="opt"><span>Cheddar-Jack Cheese, Bacon Fries</span><span>9</span></div>
      <div class="opt"><span>Chili Cheese Fries</span><span>10</span></div>
      Topped with Copper Moth Chili, cheddar jack cheese and served with chipotle crema on the side</div>
  </div>
  <div class="banner" style="left:452px;top:472px;width:196px;height:22px">SOUPS &amp; BOWLS</div>
  <div class="col" style="left:410px;top:503px;width:280px">
    <div class="item"><div class="item__head"><span>COPPER MOTH CHILI</span><span>Cup 6 | Bowl 8</span></div>Copper Moth Signature Chili with lean ground beef, black beans, and corn. Topped with cheddar cheese and green onion, served with tri-color tortilla chips.</div>
    <div class="item"><div class="item__head"><span>SOUTHWESTERN SWEET POTATO SOUP</span><span>Cup 6 | Bowl 8</span></div>A delicious mix of sweet potatoes, corn, bell peppers, and black beans, this vegan soup delivers top flavor and quality with every bowl. Served with tri-color tortilla chips.</div>
    <div class="item"><div class="item__head"><span>SOUTHWESTERN SWEET POTATO SOUP</span><span>Cup 6 | Bowl 8</span></div>Quinoa, brown rice, kale and fresh spinach, with fire roasted portobello mushrooms, zucchini and red peppers. Topped with fresh avocado, and feta cheese. Served with Lemon Champagne Vinaigrette<br><b>Add:</b> Grilled Chicken 5 | Garlic Roasted Shrimp 5</div>
  </div>

  <div class="burgerhead">GOURMET BURGERS &amp;<br>SANDWICHES</div>
  <p class="abs" style="left:782px;top:122px;width:262px;font-size:8.6px;line-height:1.17;color:var(--ink-soft)">Start with your style and then choose your protein. Our burgers are house made and cooked to your temperature. Our Fresh grilled chicken breast is marinated in house and cooked to perfection. Keep it vegetarian by choosing a vegetarian style along with the Quinoa Lentil Burger. All are served on a potato bun with lettuce, tomato, onion, and your choice of hand cut fries or sweet potato fries.</p>
  <p class="abs" style="left:782px;top:206px;width:262px;font-size:9.5px;font-weight:700;text-align:center">Premium sides available for an up charge + $2</p>
  <div class="col" style="left:782px;top:238px;width:262px">
    <div class="item"><div class="item__head"><span>CALICO CAT</span><span>12</span></div>Roasted red peppers, red onions, brie cheese, and horseradish aioli.</div>
    <div class="item"><div class="item__head"><span>TIGER CAT</span><span>12</span></div>Cheddar, Monterey Jack, and Provolone</div>
    <div class="item"><div class="item__head"><span>CAT SCRATCH FEVER</span><span>12</span></div>Guacamole, 3 pepper colby jack, pico de gallo, and chipotle mayo.</div>
    <div class="item"><div class="item__head"><span>THE FAT CAT</span><span>12</span></div>Fried egg*, bacon, cheddar cheese, and garlic aioli.</div>
    <div class="item"><div class="item__head"><span>THE SPHYNX</span><span>12</span></div>Portobello mushrooms, roasted red peppers, smoked gouda cheese, and roasted garlic aioli.</div>
    <div class="item"><div class="item__head"><span>MAINE COON</span><span>12</span></div>Grilled shrimp*, roasted corn, swiss cheese, and roasted garlic aioli.</div>
    <div class="item"><div class="item__head"><span>GRILLED SHRIMP*, ROASTED CORN, SWISS CHEESE<br>AND ROASTED</span><span>12</span></div>Whats up your alley? Choose a cheese, condiment and one topping. Additional Toppings $1 | Bacon, Egg, Shrimp - $2</div>
  </div>
  <div class="art" role="img" aria-label="Illustration of a cartoon character lounging beside a cocktail and sandwich" style="left:778px;top:500px;width:252px;height:143px"></div>
  <div class="site" style="left:782px;top:650px;width:262px">www.coppermothgrill.com</div>
</section>

</body>
</html>
```